Velundra Jobs portal

Velundra Jobs is a job portal connecting job seekers and companies offering part time jobs in the Mena region, starting in the UAE. We would like to see designs that use the color blue. We have attached images to give an idea what the website should look like. When a company posts a job the job seekers are not allowed to see which company has posted a job. There should also be a coinvex gateway. On the landing page we want a catching picture that we will send.

Target Market(s)

Students and promotional workers

Logo Text

Velundra Jobs

Coding

Coded - Design and coding required

Number of Pages Required

4 page

Font styles to use
Sans Serif

Colors
33a6d7
0692cd
85cae6

```html
<!DOCTYPE html>
<html lang="en">
<head>
<meta charset="utf-8">
<title>Velundra Jobs</title>
<link rel="stylesheet" href="https://fonts.googleapis.com/css2?family=Josefin+Sans:wght@400;600&family=Open+Sans:wght@400;600&display=swap">
<style>
  :root {
    --blue-deep: #0692cd;
    --blue-mid: #33a6d7;
    --blue-light: #85cae6;
    --teal: #4aafb3;
    --teal-btn: #4cb6bb;
    --ink: #333333;
    --ink-soft: #555555;
    --muted: #8a8a8a;
    --row: #f4f4f4;
    --line: #dedede;
    --white: #ffffff;
  }
  * { margin: 0; padding: 0; box-sizing: border-box; }
  html, body { width: 1200px; height: 862px; overflow: hidden; background: var(--white); }
  body { position: relative; font-family: "Open Sans", sans-serif; color: var(--ink); }

  .site-header { position: absolute; left: 0; top: 0; width: 1200px; height: 111px; background: var(--white); box-shadow: 0 3px 5px rgba(0,0,0,.18); }
  .brand { position: absolute; left: 150px; top: 40px; display: flex; align-items: center; gap: 8px; }
  .brand-dot { width: 14px; height: 14px; border-radius: 50%; background: var(--blue-mid); }
  .brand-name { font-family: "Open Sans", sans-serif; font-weight: 600; font-size: 22px; color: var(--blue-mid); }
  .main-nav a { position: absolute; top: 47px; font-family: "Josefin Sans", sans-serif; font-size: 16px; color: var(--ink); text-decoration: none; letter-spacing: .3px; }
  .nav-about { left: 541px; }
  .nav-contact { left: 638px; }
  .icon-bell { position: absolute; left: 750px; top: 42px; }
  .bell-badge { position: absolute; left: 765px; top: 36px; width: 19px; height: 19px; border-radius: 50%; background: var(--blue-deep); color: var(--white); font-size: 10px; font-weight: 600; display: flex; align-items: center; justify-content: center; }
  .icon-search { position: absolute; left: 810px; top: 44px; }
  .avatar { position: absolute; left: 868px; top: 29px; width: 56px; height: 56px; border-radius: 50%; border: 3px solid #e6e6e6; background: radial-gradient(circle at 50% 45%, #e8c9b3, #b78a6a 70%, #f2f2f2 72%); }
  .btn-logout { position: absolute; left: 961px; top: 38px; width: 93px; height: 37px; background: linear-gradient(var(--blue-mid), var(--blue-deep)); color: var(--white); font-family: "Josefin Sans", sans-serif; font-weight: 600; font-size: 13px; letter-spacing: .8px; display: flex; align-items: center; justify-content: center; box-shadow: 0 1px 3px rgba(0,0,0,.25); }

  .category-list { position: absolute; left: 143px; top: 129px; width: 232px; height: 595px; background: var(--blue-light); list-style: none; padding-top: 28px; }
  .category-list li { height: 33.75px; padding-left: 10px; font-size: 12.5px; font-weight: 600; color: var(--white); white-space: nowrap; }

  .filter-bar { position: absolute; left: 402px; top: 131px; width: 652px; height: 76px; background: var(--blue-light); border: 1px solid #b8dcea; }
  .field { position: absolute; top: 17px; height: 42px; width: 217px; background: var(--white); font-family: "Josefin Sans", sans-serif; font-size: 16px; padding: 13px 15px 0; }
  .field-keyword { left: 19px; color: #8c8c8c; }
  .field-district { left: 253px; color: var(--ink); }
  .field-district::after { content: ""; position: absolute; right: 20px; top: 18px; border: 5px solid transparent; border-top: 7px solid var(--ink); }
  .btn-filter { position: absolute; left: 491px; top: 16px; width: 145px; height: 41px; background: linear-gradient(var(--blue-mid), var(--blue-deep)); color: var(--white); font-size: 12.5px; font-weight: 600; letter-spacing: .8px; display: flex; align-items: center; justify-content: center; box-shadow: 0 2px 3px rgba(0,0,0,.25); }

  .job-table { position: absolute; left: 402px; top: 232px; width: 652px; border: 1px solid var(--line); border-collapse: collapse; font-size: 14px; }
  .job-table th { height: 55px; background: var(--teal); color: var(--white); font-weight: 400; text-align: left; font-size: 13.5px; }
  .job-table td { height: 55px; background: var(--row); border-top: 1px solid var(--line); color: var(--ink-soft); }
  .job-table .col-title { width: 177px; padding-left: 28px; }
  .job-table td.col-title { font-weight: 600; color: var(--ink); }
  .job-table .col-due { width: 175px; }
  .job-table th.col-due { padding-left: 3px; }
  .job-table .col-provider { width: 145px; }
  .job-table td.col-provider { padding-left: 5px; }
  .btn-apply { display: inline-flex; width: 103px; height: 40px; align-items: center; justify-content: center; background: var(--teal-btn); color: var(--white); font-size: 12.5px; font-weight: 600; letter-spacing: .9px; box-shadow: 0 2px 3px rgba(0,0,0,.2); }

  .featured-title { position: absolute; left: 401px; top: 543px; font-size: 24px; font-weight: 400; color: var(--ink); }
  .carousel-nav { position: absolute; top: 550px; width: 20px; height: 20px; border: 1px solid #9a9a9a; border-radius: 50%; }
  .carousel-prev { left: 990px; }
  .carousel-next { left: 1018px; }
  .carousel-nav svg { position: absolute; left: 6px; top: 5px; }
  .provider-card { position: absolute; top: 604px; width: 180px; }
  .provider-photo { width: 180px; height: 119px; border: 1px solid #cfcfcf; }
  .provider-name { margin-top: 9px; font-size: 14px; font-weight: 600; color: var(--ink); white-space: nowrap; }
  .card-1 { left: 402px; } .card-1 .provider-photo { background: linear-gradient(120deg, #e9cfa8, #a88566 55%, #cfd6d8); }
  .card-2 { left: 631px; } .card-2 .provider-photo { background: linear-gradient(120deg, #b9a79b, #dcdcdc 50%, #8f8b88); }
  .card-3 { left: 857px; } .card-3 .provider-photo { background: linear-gradient(120deg, #e6c7a2, #f4f4f4 45%, #9ea8b2); }

  .site-footer { position: absolute; left: 0; top: 802px; width: 1200px; border-top: 1px solid #e3e3e3; }
  .footer-text { position: absolute; right: 152px; top: 21px; font-size: 12px; color: var(--muted); white-space: nowrap; }
</style>
</head>
<body>
  <header class="site-header">
    <div class="brand"><span class="brand-dot"></span><span class="brand-name">Velundra</span></div>
    <nav class="main-nav">
      <a class="nav-about" href="#">About us</a>
      <a class="nav-contact" href="#">Contact us</a>
    </nav>
    <svg class="icon-bell" width="28" height="30" viewBox="0 0 28 30" aria-label="Notifications">
      <path d="M4 23 C7 20 7 17 7 13 C7 8 10 5 14 5 C18 5 21 8 21 13 C21 17 21 20 24 23 Z" fill="none" stroke="#222" stroke-width="1.8" stroke-linejoin="round"/>
      <path d="M11 25 Q14 29 17 25" fill="none" stroke="#222" stroke-width="1.8"/>
    </svg>
    <span class="bell-badge">20</span>
    <svg class="icon-search" width="24" height="26" viewBox="0 0 24 26" aria-label="Search">
      <circle cx="10" cy="10" r="7" fill="none" stroke="#111" stroke-width="3.5"/>
      <line x1="15" y1="16" x2="21" y2="23" stroke="#111" stroke-width="4" stroke-linecap="round"/>
    </svg>
    <div class="avatar" role="img" aria-label="Profile photo of the signed-in user"></div>
    <div class="btn-logout">LOG OUT</div>
  </header>

  <ul class="category-list">
    <li>Consulting &amp; Corp. Strategy jobs (80)</li>
    <li>Education &amp; Training jobs (3,860)</li>
    <li>Engineering jobs (13,290)</li>
    <li>Government/Defence jobs (3,015)</li>
    <li>Graduate/Entry Level jobs (2,000+)</li>
    <li>Healthcare &amp; Medical jobs (8,590)</li>
    <li>Hospitality &amp; Tourism jobs (7,096)</li>
    <li>HR &amp; Recruitment jobs (6,651)</li>
    <li>I.T. &amp; T jobs (28,745)</li>
    <li>Legal jobs (6,587)</li>
    <li>Government/Defence jobs (3,015)</li>
    <li>Graduate/Entry Level jobs (2,000+)</li>
    <li>Healthcare &amp; Medical jobs (8,590)</li>
    <li>Hospitality &amp; Tourism jobs (7,096)</li>
    <li>Education &amp; Training jobs (3,860)</li>
    <li>Government/Defence jobs (3,015)</li>
  </ul>

  <section class="filter-bar">
    <div class="field field-keyword">Keyword</div>
    <div class="field field-district">District 1</div>
    <div class="btn-filter">FILTER JOBS</div>
  </section>

  <table class="job-table">
    <thead>
      <tr><th class="col-title">JOB TITTLE</th><th class="col-due">DUE DATE</th><th class="col-provider">PROVIDER NAME</th><th></th></tr>
    </thead>
    <tbody>
      <tr><td class="col-title">Job tittle number</td><td class="col-due">due date: 23 Jan 2015</td><td class="col-provider">Provider 1</td><td><span class="btn-apply">APPLY NOW</span></td></tr>
      <tr><td class="col-title">Job tittle number</td><td class="col-due">due date: 23 Jan 2015</td><td class="col-provider">Provider 1</td><td><span class="btn-apply">APPLY NOW</span></td></tr>
      <tr><td class="col-title">Job tittle number</td><td class="col-due">due date: 23 Jan 2015</td><td class="col-provider">Provider 1</td><td><span class="btn-apply">APPLY NOW</span></td></tr>
      <tr><td class="col-title">Job tittle number</td><td class="col-due">due date: 23 Jan 2015</td><td class="col-provider">Provider 1</td><td><span class="btn-apply">APPLY NOW</span></td></tr>
    </tbody>
  </table>

  <h2 class="featured-title">Featured Job Providers</h2>
  <span class="carousel-nav carousel-prev"><svg width="7" height="9" viewBox="0 0 7 9"><path d="M5 1 L2 4.5 L5 8" fill="none" stroke="#888" stroke-width="1.2"/></svg></span>
  <span class="carousel-nav carousel-next"><svg width="7" height="9" viewBox="0 0 7 9"><path d="M2 1 L5 4.5 L2 8" fill="none" stroke="#888" stroke-width="1.2"/></svg></span>

  <div class="provider-card card-1">
    <div class="provider-photo" role="img" aria-label="Photo of a customer service agent with a headset"></div>
    <p class="provider-name">Customer Service (4)</p>
  </div>
  <div class="provider-card card-2">
    <div class="provider-photo" role="img" aria-label="Photo of an account manager working with a calculator at a desk"></div>
    <p class="provider-name">Account Manager (20)</p>
  </div>
  <div class="provider-card card-3">
    <div class="provider-photo" role="img" aria-label="Photo of a market research officer in an office"></div>
    <p class="provider-name">Market Research Officer (10)</p>
  </div>

  <footer class="site-footer">
    <p class="footer-text">© Copyright 2015 Velundra - All rights reserved | About us | Terms and conditions | Sitemap</p>
  </footer>
</body>
</html>
```